Business Card Design for Flood Rescue 360 - Property Restoration Professionals

I need a business card designed for Flood Rescue 360. We are a full-service property restoration solution. Providing water, fire, smoke & storm restoration as well as mold remediation and full remodel or reconstruction to homes and businesses across Dallas-Fort Worth, TX.
Target Market(s)
home and business owners with insurance covered property damage from water, fire or storm related damage
Industry/Entity Type
property restoration
Contact Information for Business Card
Marcus Pelley General Manager Cell: 214-555-0193 Office: 469-555-0148 email: Marcus@FloodRescue360.example services: Water, Fire, Mold, Reconstruction Tagline: Urgency for Your Water Emergency!
Look and feel
Each slider illustrates characteristics of the customer's brand and the style your logo design should communicate.

```html
<!DOCTYPE html>
<html lang="en">
<head>
<meta charset="utf-8">
<title>Flood Rescue 360 – Business Card</title>
<link href="https://fonts.googleapis.com/css2?family=Montserrat:wght@400;600;700&display=swap" rel="stylesheet">
<style>
  :root {
    --brand-blue: #00a9e6;
    --ink: #1a1a1a;
    --card-black: #141414;
    --card-white: #ffffff;
    --stage: #ecebe9;
  }
  * { box-sizing: border-box; margin: 0; padding: 0; }
  html, body { width: 1200px; height: 768px; overflow: hidden; }
  body {
    background: var(--stage);
    font-family: "Montserrat", Arial, sans-serif;
    display: flex;
    align-items: center;
    justify-content: center;
    gap: 40px;
  }
  .card {
    width: 540px;
    height: 310px;
    position: relative;
    box-shadow: 0 10px 30px rgba(0,0,0,0.15);
    overflow: hidden;
  }
  .card--front { background: var(--card-white); }
  .card--back {
    background: var(--card-black);
    display: flex;
    flex-direction: column;
    align-items: center;
    justify-content: center;
    gap: 18px;
  }

  .company-name {
    color: var(--brand-blue);
    font-weight: 600;
    font-size: 34px;
    letter-spacing: 0.5px;
    white-space: nowrap;
  }
  .card--front .company-name {
    position: absolute;
    left: 0; right: 0;
    top: 62px;
    text-align: center;
  }

  .tagline {
    color: var(--brand-blue);
    font-weight: 700;
    font-size: 13px;
    letter-spacing: 0.3px;
  }

  .contact-block {
    position: absolute;
    left: 70px;
    top: 150px;
    display: flex;
    align-items: stretch;
    gap: 16px;
  }
  .person { text-align: right; padding-top: 2px; }
  .person__name {
    color: var(--brand-blue);
    font-weight: 700;
    font-size: 19px;
  }
  .person__title {
    color: var(--ink);
    font-size: 12px;
    margin-top: 2px;
  }
  .divider { width: 1.5px; background: var(--brand-blue); }
  .contact-list { list-style: none; display: flex; flex-direction: column; gap: 5px; }
  .contact-list li {
    display: flex; align-items: center; gap: 8px;
    color: var(--ink); font-size: 12.5px;
  }
  .contact-list svg { width: 13px; height: 13px; flex: none; }

  .services {
    position: absolute;
    left: 0; right: 0;
    top: 232px;
    text-align: center;
  }
  .services__heading {
    display: inline-block;
    color: var(--brand-blue);
    font-weight: 700;
    font-size: 13px;
    border-bottom: 1.5px solid var(--brand-blue);
    padding-bottom: 1px;
    margin-bottom: 4px;
  }
  .services__row { display: flex; align-items: center; gap: 10px; }
  .services__rule { flex: 1; height: 2px; background: var(--brand-blue); }
  .services__list {
    font-weight: 700; font-size: 13px; color: var(--ink);
    white-space: nowrap;
  }
  .services__list .sep { color: var(--brand-blue); margin: 0 3px; }
</style>
</head>
<body>

  <section class="card card--front" aria-label="Business card front">
    <p class="company-name">Flood Rescue 360</p>

    <div class="contact-block">
      <div class="person">
        <p class="person__name">Marcus Pelley</p>
        <p class="person__title">General Manager</p>
      </div>
      <div class="divider"></div>
      <ul class="contact-list">
        <li>
          <svg viewBox="0 0 24 24" aria-hidden="true"><path fill="var(--brand-blue)" d="M6.6 10.8a15 15 0 0 0 6.6 6.6l2.2-2.2a1 1 0 0 1 1-.25 11.4 11.4 0 0 0 3.6.57 1 1 0 0 1 1 1V20a1 1 0 0 1-1 1A17 17 0 0 1 3 4a1 1 0 0 1 1-1h3.5a1 1 0 0 1 1 1c0 1.25.2 2.45.57 3.57a1 1 0 0 1-.25 1z"/></svg>
          214-555-0193
        </li>
        <li>
          <svg viewBox="0 0 24 24" aria-hidden="true"><rect x="4" y="9" width="16" height="12" rx="2" fill="var(--brand-blue)"/><path d="M2 8c3-4 17-4 20 0v2h-5V8H7v2H2z" fill="var(--brand-blue)"/><circle cx="12" cy="15" r="2.5" fill="#fff"/></svg>
          469-555-0148
        </li>
        <li>
          <svg viewBox="0 0 24 24" aria-hidden="true"><rect x="2" y="5" width="20" height="14" rx="1.5" fill="var(--brand-blue)"/><path d="M3 6l9 7 9-7" fill="none" stroke="#fff" stroke-width="1.6"/></svg>
          Marcus@FloodRescue360.example
        </li>
      </ul>
    </div>

    <div class="services">
      <span class="services__heading">Our Services</span>
      <div class="services__row">
        <span class="services__rule"></span>
        <span class="services__list"><span class="sep">•</span>Water<span class="sep">•</span>Fire<span class="sep">•</span>Mold<span class="sep">•</span>Reconstruction</span>
        <span class="services__rule"></span>
      </div>
    </div>
  </section>

  <section class="card card--back" aria-label="Business card back">
    <p class="company-name">Flood Rescue 360</p>
    <p class="tagline">Urgency for Your Water Emergency!</p>
  </section>

</body>
</html>
```